Podcast Cover Art for rebranded podcast - I have inspiration for the designs

I've had a podcast ("Paperboat Radio Hour") since 2018, but I'm in the process of rebranding it. I've attached the old cover art below, which I loved, but I don't need it to look like that at all. The rebranded podcast is called 'Open Window with Marnie Cole.' I've included the show description at the bottom. I've been working on various design options in Canva, but not obsessed with anything yet, but I'm attaching the ones I do like that I think just need some refining. My very favorite is the one labeled 'favorite_Open Window' so I wouldn't mind keeping that general idea but perfected by a designer. Ultimately, I want something cool, fairly clean, modern, eye catching. I'm into neutrals with maybe a pop of color, so think black, white, grey..maybe silver, and I love a pop of red..and I'm not opposed to other options for the pop color. The show is going to be inspiring, entertaining, and funny. Oh and one other idea I had but I'm not sure if it makes sense with the title and/or what the show is about..but a vinyl record with Open Window with Marnie Cole on it somehow, on a record player..not sure.

Ever wonder what it means to truly live authentically? Curious about how to embrace the unpredictability of life? Ready for some heartfelt and lighthearted conversations that inspire and entertain?
Join Marnie Cole as she dives into the raw, real, and unscripted moments of life. In each episode, Marnie brings candid conversations and genuine insights into the ups and downs we all experience. From personal growth and self-discovery to inspiring stories and valuable life lessons, "Open Window" is a space where authenticity reigns and spontaneity is celebrated.
Whether she's sharing her own journey or chatting with inspiring guests, Marnie invites you to explore the beauty of living life without a script. Expect honest reflections, thought-provoking discussions, and a refreshing perspective on navigating life's unpredictable path—all with a dash of fun and humor to keep things lively and entertaining. Step into the unscripted moments of life and tune in for a blend of depth and lightheartedness that will leave you inspired, smiling, and most importantly laughing.

Target Market(s)

25-50 year old women and men (primarily women)

Font styles to use
Sans Serif

Requirements
Should not have
• nothing too feminine or girly, nothing cheesy :)

```html
<!DOCTYPE html>
<html lang="en">
<head>
<meta charset="utf-8">
<title>Open Window with Marnie Cole – Podcast Cover</title>
<link href="https://fonts.googleapis.com/css2?family=Montserrat:wght@800;900&family=Mrs+Saint+Delafield&display=swap" rel="stylesheet">
<style>
  :root {
    --sky: #a8d3db;
    --sea: #c4e2e6;
    --foam: #e3efee;
    --sand: #ece8de;
    --teal-deep: #0a5d5c;
    --teal-mid: #1f7f7b;
    --teal-dark: #024b4a;
    --teal-soft: #5e8b8a;
    --slate: #566a6e;
    --paper: #fbfbfa;
    --pin: #d9232b;
    --figure-a: #6f8a6a;
    --figure-b: #c9d3c3;
  }
  * { margin: 0; padding: 0; box-sizing: border-box; }
  html, body { width: 1200px; height: 1200px; overflow: hidden; background: #ffffff; }
  .cover {
    position: relative;
    width: 1200px;
    height: 1200px;
    overflow: hidden;
  }
  .beach-photo {
    position: absolute; inset: 0;
    background: linear-gradient(180deg, var(--sky) 0%, var(--sea) 22%, var(--foam) 45%, #e8eeea 65%, var(--sand) 100%);
  }
  .host-photo {
    position: absolute;
    left: 704px; top: 175px;
    width: 420px; height: 880px;
    border-radius: 200px 200px 60px 60px;
    background: linear-gradient(180deg, #c9a97a 0%, #8a6c55 14%, var(--figure-a) 40%, var(--figure-b) 70%, var(--figure-a) 100%);
    opacity: .85;
    filter: blur(1px);
  }
  .title-open {
    position: absolute;
    left: 96px; top: 118px;
    font-family: "Montserrat", sans-serif;
    font-weight: 900;
    font-size: 232px;
    line-height: 1;
    letter-spacing: -6px;
    background: linear-gradient(180deg, var(--teal-mid) 0%, var(--teal-deep) 55%, var(--teal-mid) 100%);
    -webkit-background-clip: text;
    background-clip: text;
    color: transparent;
  }
  .title-script {
    position: absolute;
    left: 130px; top: 300px;
    font-family: "Mrs Saint Delafield", cursive;
    font-size: 230px;
    line-height: 1;
    color: var(--slate);
    text-shadow: 0 0 6px #ffffff, 0 0 2px #ffffff;
  }
  .snapshots { position: absolute; inset: 0; }
  .snapshot {
    position: absolute;
    background: var(--paper);
    padding: 14px 14px 22px;
    box-shadow: 0 4px 10px rgba(0,0,0,.25);
  }
  .snapshot .shot { width: 100%; height: 100%; }
  .snapshot.one { left: 80px; top: 588px; width: 248px; height: 262px; transform: rotate(2deg); }
  .snapshot.two { left: 294px; top: 608px; width: 248px; height: 262px; transform: rotate(-2deg); }
  .snapshot.three { left: 530px; top: 570px; width: 244px; height: 254px; transform: rotate(1.5deg); }
  .snapshot.one .shot { background: linear-gradient(160deg, #d9dcd8, #6b4a34 60%, #3a3330); }
  .snapshot.two .shot { background: linear-gradient(150deg, #7fa06e, #c23a2e 50%, #e8e2da); }
  .snapshot.three .shot { background: linear-gradient(160deg, #7fa27a, #2c2a2a 60%, #d8dcd6); }
  .pin { position: absolute; width: 22px; height: 30px; }
  .pin.one { left: 290px; top: 572px; }
  .pin.two { left: 480px; top: 593px; }
  .pin.three { left: 734px; top: 554px; }
  .byline-script {
    position: absolute;
    left: 92px; top: 910px;
    font-family: "Mrs Saint Delafield", cursive;
    font-size: 180px;
    line-height: 1;
    color: var(--slate);
  }
  .host-name {
    position: absolute;
    left: 343px; top: 918px;
    font-family: "Montserrat", sans-serif;
    font-weight: 900;
    font-size: 92px;
    line-height: .86;
    letter-spacing: -1px;
  }
  .host-name .first { display: block; color: var(--teal-dark); }
  .host-name .last { display: block; color: var(--teal-soft); }
</style>
</head>
<body>
<main class="cover">
  <div class="beach-photo" role="img" aria-label="Photo of a pale turquoise sea with soft waves breaking onto white sand"></div>
  <div class="host-photo" role="img" aria-label="Photo of the host seen from behind in a straw hat and leaf-print maxi dress, standing in the shallow surf"></div>

  <h1 class="title-open">OPEN</h1>
  <div class="title-script">Window</div>

  <div class="snapshots">
    <figure class="snapshot one"><div class="shot" role="img" aria-label="Snapshot of the host dancing with arms raised"></div></figure>
    <figure class="snapshot two"><div class="shot" role="img" aria-label="Snapshot of the host laughing in a red top beside a mirror"></div></figure>
    <figure class="snapshot three"><div class="shot" role="img" aria-label="Snapshot of the host smiling in a black leather jacket by a piano"></div></figure>

    <svg class="pin one" viewBox="0 0 22 30" aria-hidden="true"><circle cx="11" cy="8" r="8" fill="var(--pin)"/><rect x="7" y="14" width="8" height="6" rx="2" fill="var(--pin)"/><circle cx="11" cy="22" r="5" fill="var(--pin)"/><circle cx="8" cy="6" r="2.5" fill="#ff8a8a"/></svg>
    <svg class="pin two" viewBox="0 0 22 30" aria-hidden="true"><circle cx="11" cy="8" r="8" fill="var(--pin)"/><rect x="7" y="14" width="8" height="6" rx="2" fill="var(--pin)"/><circle cx="11" cy="22" r="5" fill="var(--pin)"/><circle cx="8" cy="6" r="2.5" fill="#ff8a8a"/></svg>
    <svg class="pin three" viewBox="0 0 22 30" aria-hidden="true"><circle cx="11" cy="8" r="8" fill="var(--pin)"/><rect x="7" y="14" width="8" height="6" rx="2" fill="var(--pin)"/><circle cx="11" cy="22" r="5" fill="var(--pin)"/><circle cx="8" cy="6" r="2.5" fill="#ff8a8a"/></svg>
  </div>

  <div class="byline-script">With</div>
  <p class="host-name"><span class="first">MARNIE</span><span class="last">COLE</span></p>
</main>
</body>
</html>
```